Business card for a Exhibition booth fabrication company

Hi. My company would like to change our corporate name card. We are an events and Exhibition stand builder company. We would like our corporate name card to resonate what we do. I need someone to create something unique that relates to the industry that I am in. The graphic designer should be creative to incorporate the elements of my industry and try to blend in well in the design of the card. Our aim is to ensure that we are unique and our card can look different from our competitors.
Updates

Target Market(s)

Marketing and events manager from all companies

Contact Information for Business Card

The business card should have the following details:
Name
Job Title
Email
Website

Colors

Designer to choose colors to be used in the design.

Requirements
Must have
• The card must be look something that is relevant to the service that I am providing. My website is: www.velmora-buildworks.com
• You can see my website to get more information on what service that I am doing
Nice to have
• On the back of my card, I would like to have a globe image with the incorporation of my company logo. This is to indicate that my services can be done in any part of the world.

```html
<!DOCTYPE html>
<html lang="en">
<head>
<meta charset="utf-8">
<title>Velmora Buildworks – Business Card</title>
<link rel="stylesheet" href="https://fonts.googleapis.com/css2?family=Arimo:wght@700&family=Open+Sans:wght@400;600;700&display=swap">
<style>
  :root {
    --brand-red: #ed1c24;
    --ink-grey: #58595b;
    --swoosh-grey: #6d6e71;
    --card-white: #ffffff;
    --stage-light: #dedfe2;
    --stage-dark: #a3a4a8;
    --map-top: #dcdcde;
    --map-mid: #e9e9ea;
  }
  * { margin: 0; padding: 0; box-sizing: border-box; }
  html, body { width: 1200px; height: 1118px; overflow: hidden; }
  body {
    background: linear-gradient(90deg, var(--stage-light), var(--stage-dark));
    position: relative;
    font-family: "Open Sans", Arial, sans-serif;
  }
  .card {
    position: absolute;
    left: 223px;
    width: 754px;
    height: 430px;
    background: var(--card-white);
    border-radius: 34px;
    overflow: hidden;
  }
  .card--front { top: 88px; }
  .card--back { top: 566px; }

  .holder { position: absolute; left: 52px; top: 86px; }
  .holder__name {
    font-family: "Arimo", Arial, sans-serif;
    font-weight: 700;
    font-size: 26px;
    color: var(--brand-red);
    line-height: 1;
  }
  .holder__title {
    margin-top: 12px;
    font-size: 19px;
    letter-spacing: 0.5px;
    color: var(--ink-grey);
    line-height: 1;
  }
  .contacts { position: absolute; left: 50px; top: 177px; list-style: none; }
  .contacts__item {
    display: flex; align-items: center; gap: 10px;
    height: 35px;
    font-size: 18px; color: var(--ink-grey);
  }
  .contacts__icon { width: 20px; height: 20px; flex: none; }

  .brand-name {
    position: absolute;
    left: 383px; top: 214px; width: 340px;
    text-align: center;
    font-size: 21px; font-weight: 600;
    letter-spacing: 2.6px;
    color: var(--ink-grey);
    white-space: nowrap;
    line-height: 1.2;
  }

  .wave { position: absolute; left: 0; top: 0; width: 754px; height: 430px; }

  .address {
    position: absolute; left: 63px; top: 360px;
    font-size: 18px; line-height: 29px;
    color: var(--card-white);
  }

  .globe-map {
    position: absolute;
    left: 0; top: 0;
    width: 754px; height: 430px;
  }
  .floor-shadow {
    position: absolute;
    left: 70px; top: 344px;
    width: 620px; height: 46px;
    border-radius: 50%;
    background: radial-gradient(ellipse at center, #d9d9db 0%, rgba(255,255,255,0) 70%);
  }
  .brand-name--back {
    left: 170px; top: 276px; width: 414px;
    font-size: 26px; font-weight: 700;
    letter-spacing: 2px;
    color: var(--brand-red);
  }
  .web-line {
    position: absolute;
    left: 0; top: 384px; width: 754px;
    text-align: center;
    font-size: 20px; letter-spacing: 4px;
    color: #3a3a3c;
    line-height: 1.2;
  }
</style>
</head>
<body>

<section class="card card--front">
  <svg class="wave" viewBox="0 0 754 430" aria-hidden="true">
    <path d="M0,336 C180,308 400,335 560,382 C650,406 715,404 754,394" fill="none" stroke="var(--brand-red)" stroke-width="3"/>
    <path d="M0,350 C200,322 420,352 560,393 C650,418 720,418 754,408 L754,430 L0,430 Z" fill="var(--brand-red)"/>
    <path d="M110,328 C320,304 470,344 620,384 C690,402 730,394 754,382 L754,398 C730,410 690,414 620,398 C470,358 320,316 110,328 Z" fill="var(--swoosh-grey)"/>
  </svg>

  <div class="holder">
    <h1 class="holder__name">DARREN HOLLOWAY</h1>
    <p class="holder__title">PRESIDENT</p>
  </div>

  <ul class="contacts">
    <li class="contacts__item">
      <svg class="contacts__icon" viewBox="0 0 20 20" aria-hidden="true"><path d="M5 2l3 4-2 2c1 2.5 3.5 5 6 6l2-2 4 3-2 3C9 18 2 11 2 4z" fill="var(--brand-red)"/></svg>
      012-345-6789
    </li>
    <li class="contacts__item">
      <svg class="contacts__icon" viewBox="0 0 20 20" aria-hidden="true"><rect x="2" y="5" width="16" height="11" fill="var(--brand-red)"/><path d="M2 5l8 6 8-6M2 16l6-5M18 16l-6-5" stroke="#fff" stroke-width="1.4" fill="none"/></svg>
      info@velmorabuildworks.com
    </li>
    <li class="contacts__item">
      <svg class="contacts__icon" viewBox="0 0 20 20" aria-hidden="true"><g fill="none" stroke="var(--brand-red)" stroke-width="1.6"><circle cx="10" cy="10" r="8"/><ellipse cx="10" cy="10" rx="3.5" ry="8"/><path d="M2 10h16M3.5 6h13M3.5 14h13"/></g></svg>
      www.velmora-buildworks.com
    </li>
  </ul>

  <p class="brand-name">VELMORA BUILDWORKS</p>

  <p class="address">Street Name, City Name<br>Zipcode - 01234</p>
</section>

<section class="card card--back">
  <svg class="globe-map" viewBox="0 0 754 430" role="img" aria-label="Grey world map curving over the top of a globe">
    <defs>
      <linearGradient id="globe-fade" x1="0" y1="0" x2="0" y2="1">
        <stop offset="0" stop-color="var(--map-top)"/>
        <stop offset="0.6" stop-color="var(--map-mid)"/>
        <stop offset="1" stop-color="#ffffff" stop-opacity="0"/>
      </linearGradient>
    </defs>
    <path d="M47,262 A335 210 0 0 1 717,262 Z" fill="url(#globe-fade)"/>
  </svg>
  <div class="floor-shadow" aria-hidden="true"></div>
  <p class="brand-name brand-name--back">VELMORA BUILDWORKS</p>
  <p class="web-line">www.velmora-buildworks.com</p>
</section>

</body>
</html>
```